Print Ad for 2024 Bright Ledger Magazine - Show Us Something Unique!

We need an advertisement for back cover of the Bright Ledger annual publication, which will also be included as a featured ad in the Harrowgate Review, a widely-read, stylish city magazine.

We have a reputation for our originality, personality, and style and 2024 is no different. We want a design that is clever, stylish, unexpected and/or unique.

The one thing we DO NOT WANT is to look like a traditional law firm. We are NOT stuffy old white men. We skip designs that are boring, traditional, or expected. We separate ourselves in our market by NOT acting like a traditional law firm.

More about us: Maldrenko Fairweather and Quist, LLC provides full-service legal representation to entrepreneurs, individuals, and companies for all of their business, employment and litigation needs.

We have included several different photo options. Please use ONLY ONE in the ad.

BE SURE TO REVIEW THE ATTACHMENTS. WE HAVE INCLUDED OUR ADS FOR PRIOR YEARS, BUT WE WANT A TOTALLY DIFFERENT LOOK THIS YEAR!! PLEASE DO NOT PROVIDE SIMILAR ADS.

Target Market(s)

Small business owners, individuals with employment law issues, entrepreneurs, other attorneys.

Industry/Entity Type

Law

Font styles to use
Serif
Sans Serif
Decorative

Requirements
Must have
• It must use our logo, our photo, and our tag line "The Name is Hard to Remember. The Results are Hard to Forget." 1. Use our full firm name of Jeselskis Brinkerhoff and Joseph, LLC2. Use our logo, attached AND our slogan - "THE NAME IS HARD TO REMEMBER. THE RESULTS ARE HARD TO FORGET." Please review the PDF attachments on the ad specs. The ad must follow the following requirements:• COLOR: Must be provided as CMYK, please convert if necessary. • IMAGES: All images must be precisely 300 dpi, placed at 100% to ensure print quality.• LOGOS: Preferred vector (.eps) format, (acceptable as high-res 300 dpi image).• TEXT: Should be editable within the ad. • BRIGHT LEDGER REFERENCES: Please adhere to the attached advertising guidelines regarding the appropriate use of the Bright Ledger name, ad concepts and imagery.
Nice to have
• Highly stylized, memorable, upscale look. We really want to show our personality. We take our work seriously, but we don't take ourselves too seriously.
Should not have
• PLEASE REVIEW UPDATED AD SPECS IN ATTACHMENT! Scales of justice, traditional law firm style, or other design features that are predictable in law firm advertising. We don't like clutter or narrative copy.

```html
<!DOCTYPE html>
<html lang="en">
<head>
<meta charset="utf-8">
<title>Maldrenko Fairweather and Quist, LLC — Print Ad</title>
<link rel="stylesheet" href="https://fonts.googleapis.com/css2?family=Montserrat:wght@900&family=Ubuntu:wght@400;500&family=Kalam:wght@700&display=swap">
<style>
  :root {
    --navy: #13164f;
    --navy-deep: #0c0e36;
    --yellow: #f6d41c;
    --sky: #dcedf6;
    --paper: #f4f8fa;
    --red: #e4161b;
    --white: #ffffff;
    --ink-soft: #40436e;
  }
  html, body { margin: 0; padding: 0; overflow: hidden; background: #fff; }
  .ad {
    position: relative;
    width: 921px;
    height: 1200px;
    overflow: hidden;
    background: linear-gradient(180deg, var(--paper) 0%, var(--sky) 100%);
  }
  .ad svg { position: absolute; inset: 0; display: block; }
  .brand { font-family: "Ubuntu", sans-serif; font-weight: 500; font-size: 26px; fill: var(--navy); }
  .contact { font-family: "Ubuntu", sans-serif; font-weight: 500; font-size: 22px; fill: var(--navy); text-anchor: end; }
  .tag-big { font-family: "Montserrat", sans-serif; font-weight: 900; font-size: 64px; }
  .tag-small { font-family: "Montserrat", sans-serif; font-weight: 900; font-size: 30px; fill: var(--white); }
  .award-name { font-family: "Kalam", cursive; font-weight: 700; font-size: 20px; fill: var(--navy); text-anchor: middle; }
  .award-line { font-family: "Ubuntu", sans-serif; font-weight: 500; font-size: 13px; fill: var(--navy); text-anchor: middle; }
  .award-year { fill: var(--ink-soft); font-weight: 400; }
  .service { font-family: "Ubuntu", sans-serif; font-weight: 500; font-size: 18px; fill: var(--navy); }
  .firm-name { font-family: "Ubuntu", sans-serif; font-weight: 500; font-size: 24px; fill: var(--navy); text-anchor: middle; }
</style>
</head>
<body>
<div class="ad">
<svg width="921" height="1200" viewBox="0 0 921 1200" xmlns="http://www.w3.org/2000/svg">
  <defs>
    <linearGradient id="teamPhoto" x1="0" x2="1" y1="0" y2="1">
      <stop offset="0" stop-color="#c9cfc4"/>
      <stop offset="0.55" stop-color="#b8a99a"/>
      <stop offset="1" stop-color="#7d93b8"/>
    </linearGradient>
  </defs>

  <!-- Header: firm mark and contact -->
  <g class="header">
    <circle cx="58" cy="70" r="22" fill="var(--navy)"/>
    <text class="brand" x="92" y="79">MFQ Legal</text>
    <text class="contact" x="650" y="78">www.mfqlegal.com</text>
    <text class="contact" x="838" y="78">555-014-2290</text>
    <g class="phone-icon" transform="translate(850 55)" fill="var(--navy)">
      <path d="M4 3 C1 5 0 10 3 15 C6 20 11 24 17 26 C20 27 23 25 24 22 L20 18 L17 21 C13 19 9 15 7 11 L10 8 Z"/>
      <path d="M15 3 A10 10 0 0 1 24 12" fill="none" stroke="var(--navy)" stroke-width="2.2"/>
    </g>
    <rect x="40" y="108" width="841" height="4" fill="var(--yellow)"/>
  </g>

  <!-- Single team photograph -->
  <rect x="40" y="134" width="841" height="426" rx="18" fill="url(#teamPhoto)" role="img" aria-label="Team photo of the five attorneys: Greta Lindqvist Quist, Owen Pratt, TR Fairweather, Marisol Maldrenko and Delia R. Marsh"/>

  <!-- Tagline band -->
  <rect x="0" y="584" width="921" height="236" fill="var(--navy)"/>
  <rect x="0" y="584" width="14" height="236" fill="var(--yellow)"/>
  <g class="tagline">
    <text class="tag-big" x="60" y="652" fill="var(--white)">THE NAME</text>
    <text class="tag-small" x="60" y="690">IS HARD TO REMEMBER.</text>
    <text class="tag-big" x="60" y="764" fill="var(--yellow)">THE RESULT</text>
    <text class="tag-small" x="60" y="802">ARE HARD TO FORGET.</text>
  </g>

  <!-- Recognition -->
  <g class="awards">
    <g class="award">
      <rect x="57" y="846" width="160" height="3" fill="var(--red)"/>
      <text class="award-name" x="137" y="878">Greta Lindqvist Quist</text>
      <text class="award-line" x="137" y="902">Bright Ledger</text>
      <text class="award-line" x="137" y="920">Top 25 Women <tspan class="award-year">2023-2024</tspan></text>
      <text class="award-line" x="137" y="938">Bright Ledger Top 50 <tspan class="award-year">2024</tspan></text>
      <text class="award-line" x="137" y="956">Bright Ledger <tspan class="award-year">2018 – 2024</tspan></text>
      <text class="award-line" x="137" y="974">Emerging Talent <tspan class="award-year">2013 – 2017</tspan></text>
    </g>
    <g class="award">
      <rect x="272" y="846" width="160" height="3" fill="var(--red)"/>
      <text class="award-name" x="352" y="878">Marisol Maldrenko</text>
      <text class="award-line" x="352" y="902">Bright Ledger</text>
      <text class="award-line" x="352" y="920">Top 25 Women <tspan class="award-year">2019, 2022-2024</tspan></text>
      <text class="award-line" x="352" y="938">Bright Ledger Top 50 <tspan class="award-year">2024</tspan></text>
      <text class="award-line" x="352" y="956">Bright Ledger <tspan class="award-year">2015 – 2023</tspan></text>
      <text class="award-line" x="352" y="974">Emerging Talent <tspan class="award-year">2011 – 2013</tspan></text>
    </g>
    <g class="award">
      <rect x="488" y="846" width="160" height="3" fill="var(--red)"/>
      <text class="award-name" x="568" y="878">TR Fairweather</text>
      <text class="award-line" x="568" y="902">Bright Ledger <tspan class="award-year">2019 – 2024</tspan></text>
      <text class="award-line" x="568" y="920">Emerging Talent <tspan class="award-year">2014, 2018</tspan></text>
    </g>
    <g class="award">
      <rect x="703" y="846" width="160" height="3" fill="var(--red)"/>
      <text class="award-name" x="783" y="878">Delia R. Marsh</text>
      <text class="award-line" x="783" y="902">Emerging Talent <tspan class="award-year">2014, 2018</tspan></text>
    </g>
  </g>

  <!-- Practice areas and firm name -->
  <rect x="0" y="1018" width="921" height="182" fill="var(--yellow)"/>
  <text class="service" x="60" y="1062">· Business Litigation &amp; Dispute Resolution</text>
  <text class="service" x="60" y="1092">· Entrepreneurship &amp; Small Business</text>
  <text class="service" x="520" y="1062">· Employment &amp; Labor</text>
  <text class="service" x="520" y="1092">· Contract and Commercial Law</text>
  <rect x="60" y="1118" width="801" height="2" fill="var(--navy)" opacity="0.35"/>
  <text class="firm-name" x="460" y="1162">Maldrenko Fairweather and Quist, LLC</text>
</svg>
</div>
</body>
</html>
```